Sophisticated, clean website reflecting my feminine, playful side to sell my abstract art,

I need a website no more than 3 pages to showcase my paintings, a little about me and some contact info. I do abstracts so looking for something a little edgy, yet feminine and current.
Updates

Hi there, These are some artists websites that I Iike: Marnelvoss.com (I like how airy it is) peterwallombry.com garethpolvens.com (I like how it scrolls) I'll need a place for a photo ( a headshot-i do not have it yet so I'll need to be able to upload that later) as well as an area for my bio. Also, it's important that I will be able to upload any new photos and descriptions easily so it should be user friendly. Lastly, I like in a sunny place so would like to have this seem upbeat and playful as that is how i like to paint. thanks-I'm trying to upload my photos now -

Target Market(s)

ppl ages 35-70 who want large scale art for their homes

Industry/Entity Type

art

Coding

Coded - Design and coding required

Number of Pages Required

3 page

Colors

Designer to choose colors to be used in the design.

Requirements
Must have
• photos of my art, a place for my bio, be easy to reach me. tasteful-nothing too "in your face" -my clients are pretty high end and organized. They like clean lines
Nice to have
• sophisticated background, muted tones in the back-similar clean font throughout-no cursive
Should not have
• too many dark areas. Too many blocks of color. Too serious.

```html
<!DOCTYPE html>
<html lang="en">
<head>
<meta charset="utf-8">
<title>Clara Wendell — Art Gallery</title>
<link rel="stylesheet" href="https://fonts.googleapis.com/css2?family=Playfair+Display:wght@400;700&family=Source+Sans+3:wght@400;600;700&display=swap">
<style>
:root{
  --ink:#111;
  --paper:#fff;
  --line:#c9c9c9;
  --frame:#8a8a8a;
  --footer:#232323;
  --footer-text:#e9e9e9;
  --sage:#9a9c82;
  --serif:"Playfair Display", Georgia, serif;
  --sans:"Source Sans 3", "Source Sans Pro", Arial, sans-serif;
}
*{box-sizing:border-box;margin:0;padding:0}
html,body{width:1200px;height:3755px;overflow:hidden;background:var(--paper)}
body{position:relative;font-family:var(--sans);color:var(--ink)}
.abs{position:absolute}
.round-icon{position:absolute;width:32px;height:32px;border:1.5px solid var(--ink);border-radius:50%;display:flex;align-items:center;justify-content:center}
.round-icon svg{width:15px;height:15px}
.site-title{left:0;width:1200px;top:20px;text-align:center;font-family:var(--serif);font-size:32px;font-weight:400}
.login-btn{left:974px;top:17px;width:124px;height:49px;border:1.5px solid var(--frame);display:flex;align-items:center;justify-content:center;font-weight:700;font-size:15px}
.main-nav{left:0;width:1200px;top:84px;display:flex;justify-content:center;gap:25px;font-size:11px;font-weight:600}
.main-nav .current{text-decoration:underline}
.hero{left:0;top:131px;width:1200px;height:499px;background:linear-gradient(100deg,#a07a56 0%,#a07a56 7%,#e8e4ea 8%,#3f9a4a 20%,#2d8a4e 38%,#7fbf57 55%,#c7c26a 70%,#8fbd5a 85%,#2b6e5a 100%)}
.hero-title{left:0;width:1200px;top:275px;text-align:center;font-family:var(--serif);font-weight:700;font-size:48px;color:#fff}
.outline-btn{position:absolute;display:flex;align-items:center;justify-content:center;font-weight:700;font-size:15px;border:1.5px solid var(--frame);background:#fff}
.hero-btn{left:506px;top:369px;width:187px;height:49px;border:none}
.hero-dots{left:0;width:1200px;top:592px;display:flex;justify-content:center;gap:6px}
.hero-dots span{width:12px;height:12px;border-radius:50%;background:#555}
.hero-dots span.active{background:#111}
.hero-dots span.faint{background:rgba(255,255,255,.45)}
.artist-photo{left:0;top:630px;width:593px;height:605px;background:radial-gradient(ellipse at 55% 45%,#d6b27a 0%,#8a6a44 35%,#3d3428 70%,#2a2620 100%)}
.section-heading{font-family:var(--serif);font-weight:400;font-size:35px}
.about-heading{left:662px;top:718px}
.about-text{left:662px;top:818px;width:436px;font-size:14px;line-height:22.6px}
.gallery-heading{left:0;width:1200px;top:1327px;text-align:center}
.art-left{left:0;top:1499px;width:334px;height:500px;background:linear-gradient(120deg,#efe9dc,#d8c48a 40%,#e7e1d3 60%,#c9a97f 100%)}
.art-center{left:366px;top:1436px;width:468px;height:626px;background:linear-gradient(90deg,#1c8a8a 0%,#1c8a8a 12%,#d9d3c6 14%,#cfc9bb 60%,#1d3f8a 72%,#142e6e 100%)}
.art-right{left:866px;top:1499px;width:334px;height:500px;background:radial-gradient(circle at 50% 55%,#d9ad3c 0%,#e1c772 40%,#ece7d6 75%,#c4573a 100%)}
.contact-card{left:101px;top:2155px;width:997px;height:560px;border:1.5px solid var(--frame)}
.card-name{left:150px;top:2400px;width:250px;text-align:center;font-family:var(--serif);font-size:34px;font-weight:700;line-height:1.1}
.hello-heading{left:481px;width:513px;top:2247px;text-align:center}
.field{position:absolute;border-bottom:1.5px solid var(--line);font-size:14px;padding-bottom:10px;color:#333}
.snap-heading{left:0;width:1200px;top:2808px;text-align:center}
.feed-tile{top:2917px;width:240px;height:207px}
.feed-1{left:103px;background:radial-gradient(circle at 55% 50%,#4a3aa0,#8b6bc0 40%,#e9e4ec 80%)}
.feed-2{left:356px;background:radial-gradient(circle at 45% 55%,#a4391c,#c56a44 45%,#efe5de 85%)}
.feed-3{left:608px;background:radial-gradient(circle at 55% 60%,#d99a8f,#c3848c 45%,#6b3c34 90%)}
.feed-4{left:859px;background:radial-gradient(circle at 55% 50%,#c88a96,#d9a8ae 50%,#7d5556 95%)}
.follow-btn{left:507px;top:3187px;width:187px;height:50px}
.site-footer{left:0;top:3331px;width:1200px;height:424px;background:var(--footer);color:var(--footer-text)}
.footer-name{left:99px;top:3470px;width:200px;font-family:var(--serif);font-size:40px;font-weight:700;color:#fff;line-height:1.1}
.footer-heading{font-family:var(--serif);font-size:23px;top:3426px;color:#fff}
.quick-links a{position:absolute;left:385px;font-size:14px;color:var(--footer-text);text-decoration:none}
.footer-icon{position:absolute;width:30px;height:30px;border:1.5px solid #ddd;border-radius:50%;display:flex;align-items:center;justify-content:center}
.footer-icon svg{width:14px;height:14px}
.contact-line{position:absolute;left:608px;font-size:14px}
.newsletter-input{left:821px;top:3488px;width:195px;height:62px;background:#fff;color:#333;font-size:11px;padding:0 24px;display:flex;align-items:center}
.newsletter-send{left:1016px;top:3488px;width:82px;height:62px;background:var(--sage);display:flex;align-items:center;justify-content:center}
.legal{top:3712px;font-size:10px;color:#ddd}
</style>
</head>
<body>

<header>
  <div class="round-icon" style="left:101px;top:25px" role="img" aria-label="Social profile link"></div>
  <div class="round-icon" style="left:144px;top:25px" role="img" aria-label="Social profile link"></div>
  <div class="round-icon" style="left:188px;top:25px" role="img" aria-label="Social profile link"></div>
  <div class="round-icon" style="left:232px;top:25px" aria-label="Email">
    <svg viewBox="0 0 16 16" fill="none" stroke="#111" stroke-width="1.4"><rect x="1.5" y="3" width="13" height="10" rx="1"/><path d="M2 4l6 5 6-5"/></svg>
  </div>
  <div class="round-icon" style="left:276px;top:25px" aria-label="Phone">
    <svg viewBox="0 0 16 16" fill="none" stroke="#111" stroke-width="1.4"><path d="M3 2h3l1.5 3.5-2 1.2a8 8 0 0 0 3.8 3.8l1.2-2L14 10v3a1 1 0 0 1-1 1A11 11 0 0 1 2 3a1 1 0 0 1 1-1z"/></svg>
  </div>

  <div class="abs site-title">Clara Wendell</div>

  <div class="round-icon" style="left:822px;top:25px" aria-label="Account">
    <svg viewBox="0 0 16 16" fill="#111"><circle cx="8" cy="5.5" r="3"/><path d="M2.5 14a5.5 5 0 0 1 11 0z"/></svg>
  </div>
  <div class="round-icon" style="left:866px;top:25px" aria-label="Wishlist">
    <svg viewBox="0 0 16 16" fill="none" stroke="#111" stroke-width="1.4"><path d="M8 13.5S2 10 2 6a3 3 0 0 1 6-1 3 3 0 0 1 6 1c0 4-6 7.5-6 7.5z"/></svg>
  </div>
  <div class="round-icon" style="left:910px;top:25px" aria-label="Cart">
    <svg viewBox="0 0 16 16" fill="none" stroke="#111" stroke-width="1.4"><path d="M1 2h2l2 8h8l1.5-6H4"/><circle cx="6" cy="13" r="1"/><circle cx="12" cy="13" r="1"/></svg>
  </div>
  <div class="abs login-btn">Login</div>

  <nav class="abs main-nav">
    <span class="current">Home</span><span>Reviews</span><span>Art Gallery</span><span>Collection</span><span>About The Artist</span><span>Contact</span>
  </nav>
</header>

<section>
  <div class="abs hero" role="img" aria-label="Close-up of a green, teal and yellow abstract painting"></div>
  <h1 class="abs hero-title">Welcome To My Art Gallery</h1>
  <div class="outline-btn hero-btn">Explore All</div>
  <div class="abs hero-dots"><span class="faint"></span><span></span><span class="active"></span><span></span><span class="faint"></span></div>
</section>

<section>
  <div class="abs artist-photo" role="img" aria-label="Portrait photo of the artist"></div>
  <h2 class="abs section-heading about-heading">About The Artist</h2>
  <p class="abs about-text">Lorem ipsum dolor sit amet, consectetur adipiscing elit. Consequat quis turpis adipiscing tincidunt. Fames ut lectus tempus quis lacus nunc arcu. Mi, ultrices varius ultrices massa aliquam odio enim quam. Quisque libero sed eget pellentesque imperdiet. At et lorem habitant amet morbi velit, sed eu lorem. Egestas egestas mattis ultrices aliquam. Malesuada at malesuada convallis feugiat. Pharetra venenatis odio duis quis semper amet. Amet justo, enim ac lacus, aenean elementum. Commodo fermentum viverra consectetur at elit mauris a orci. Quis molestie cursus nisi lorem mi.<br>Suscipit cursus sagittis odio ut sit in aliquam at amet. Leo orci sed mauris sit morbi mi diam vestibulum. Ultrices aliquam donec semper gravida nibh dictum dui. Suspendisse ultrices egestas dui a, faucibus. Eget a id placerat semper consectetur. Integer augue tortor etiam quis. Euismod imperdiet elit proin fames felis lectus justo.</p>
</section>

<section>
  <h2 class="abs section-heading gallery-heading">Art Gallery</h2>
  <div class="abs art-left" role="img" aria-label="Abstract painting with pale swirls leaning on wood"></div>
  <div class="abs art-center" role="img" aria-label="Abstract painting in teal, linen and deep blue"></div>
  <div class="abs art-right" role="img" aria-label="Abstract painting in mustard yellow and rust swirls"></div>
</section>

<section>
  <div class="abs contact-card"></div>
  <div class="abs card-name">Clara<br>Wendell</div>
  <h2 class="abs section-heading hello-heading">Say Hello!</h2>
  <div class="field" style="left:481px;top:2362px;width:203px">First Name</div>
  <div class="field" style="left:790px;top:2362px;width:204px">Last Name</div>
  <div class="field" style="left:481px;top:2428px;width:513px">Email Address</div>
  <div class="field" style="left:481px;top:2493px;width:513px">Message</div>
  <div class="outline-btn" style="left:481px;top:2573px;width:187px;height:49px">Send</div>
</section>

<section>
  <h2 class="abs section-heading snap-heading">Follow Me On Snapfolio</h2>
  <div class="abs feed-tile feed-1" role="img" aria-label="Purple and violet abstract painting"></div>
  <div class="abs feed-tile feed-2" role="img" aria-label="Rust red swirl painting"></div>
  <div class="abs feed-tile feed-3" role="img" aria-label="Pink and brown floral abstract"></div>
  <div class="abs feed-tile feed-4" role="img" aria-label="Pink rose abstract painting"></div>
  <div class="outline-btn follow-btn">Follow</div>
</section>

<footer class="abs site-footer"></footer>
<div class="abs footer-name">Clara<br>Wendell</div>

<h3 class="abs footer-heading" style="left:385px">Quick Links</h3>
<div class="quick-links">
  <a style="top:3486px">Home</a>
  <a style="top:3517px">Featured Collection</a>
  <a style="top:3549px">Reviews</a>
  <a style="top:3580px">Art Gallery</a>
  <a style="top:3612px">About The Artist</a>
</div>

<h3 class="abs footer-heading" style="left:557px">Contact Info</h3>
<div class="footer-icon" style="left:558px;top:3487px">
  <svg viewBox="0 0 16 16" fill="none" stroke="#eee" stroke-width="1.4"><path d="M3 2h3l1.5 3.5-2 1.2a8 8 0 0 0 3.8 3.8l1.2-2L14 10v3a1 1 0 0 1-1 1A11 11 0 0 1 2 3a1 1 0 0 1 1-1z"/></svg>
</div>
<div class="contact-line" style="top:3492px">000.000.0000</div>
<div class="footer-icon" style="left:558px;top:3531px">
  <svg viewBox="0 0 16 16" fill="#eee"><path d="M8 1a5 5 0 0 0-5 5c0 4 5 9 5 9s5-5 5-9a5 5 0 0 0-5-5zm0 7a2 2 0 1 1 0-4 2 2 0 0 1 0 4z"/></svg>
</div>
<div class="contact-line" style="top:3536px">gfgfsgfgddhgjhytrtshgjhfd</div>
<div class="footer-icon" style="left:558px;top:3575px">
  <svg viewBox="0 0 16 16" fill="none" stroke="#eee" stroke-width="1.4"><rect x="1.5" y="3" width="13" height="10" rx="1"/><path d="M2 4l6 5 6-5"/></svg>
</div>
<div class="contact-line" style="top:3580px">claraw123@wendellart.com</div>

<h3 class="abs footer-heading" style="left:821px">Newsletter</h3>
<div class="abs newsletter-input">Email</div>
<div class="abs newsletter-send">
  <svg width="24" height="24" viewBox="0 0 24 24" fill="none" stroke="#fff" stroke-width="1.5"><path d="M21 3L3 10l7 3 3 7z"/><path d="M21 3L10 13"/></svg>
</div>
<div class="footer-icon" style="left:820px;top:3583px" role="img" aria-label="Social profile link"></div>
<div class="footer-icon" style="left:864px;top:3583px" role="img" aria-label="Social profile link"></div>
<div class="footer-icon" style="left:908px;top:3583px" role="img" aria-label="Social profile link"></div>

<div class="abs legal" style="left:103px">Terms Of Use</div>
<div class="abs legal" style="left:197px">Privacy Policy</div>
<div class="abs legal" style="right:102px">© 2022 Art Gallery. ALL RIGHTS RESERVED</div>

</body>
</html>
```